Design letter head and business card

Hello,

you should design a business card and letter paper for Kranichflug Marketing. In German we write this word with K insteat of C.

Company does not have a logo. But in general, we write Kranichflug Marketing in 2 lines.
First line red: KRANICHFLUG
Second line gray: MARKETING

Red (or wine red) and Gray / Black are our favorite colors.

Company slogan: "Fresh Ground Online Marketing".

Company offers SEO, SEM, SEA, AdWords, Conversion Optimization, Online Markting Consulting ...

The website is old, please do not use this as base for your task.

German letter paper sizes:
Viawable Dimensions : 210 x 297 mm
Needed file dimensions: 212 x 299 mm

Informations to include:

Address:
Kranichflug Marketing GmbH
Lindenweg 23
71592 Rebenfeld
Germany

Geschäftsführer | CEO: Bernhard Olzner

Phone: +49 (0) 7421 846 27 05

Fax: +49 (0) 7421 846 27 88

Mail: info@kranichflug-beispiel.de

Web: www.kranichflug-beispiel.de

Amtsgericht Suttgart, HRB 537264

Bank: Rosenauer Bank
IBAN: DE827315480900XXXXXXXX
BIC: GENODES1RSQ

Thanks

Bernhard

Target Market(s)

People who likes to win the online marketing game.

Industry/Entity Type

Business

Contact Information for Business Card

Here is the personal text on the card:

Name:
Bernhard Olzner

Title:
Geschäftsführer | CEO

Address:
Kranichflug Marketing GmbH
Lindenweg 23
71592 Rebenfeld
Germany

Phone:
+49 (0) 7421 846 27 05

Fax:
+49 (0) 7421 846 27 88

Mail:
olzner@kranichflug-beispiel.de

Web:
www.kranichflug-beispiel.de

Business Card:
Viewable Dimensions: 85 x 55 mm
Needed file dimensions: 87 x 57mm

Font styles to use
Sans Serif

Requirements
Nice to have
• It would be great to see the dynamics of a helicopter.

```html
<!DOCTYPE html>
<html lang="de">
<head>
<meta charset="utf-8">
<title>Kranichflug Marketing – Visitenkarte</title>
<link href="https://fonts.googleapis.com/css2?family=Oswald:wght@600;700&family=Pathway+Gothic+One&display=swap" rel="stylesheet">
<style>
  :root {
    --page: #ffffff;
    --card: #e6e6e7;
    --stripe-gray: #a7a8ab;
    --wine: #8c1f22;
    --ink: #2b2b2b;
    --mark-gray: #b9b9bb;
  }
  * { margin: 0; padding: 0; box-sizing: border-box; }
  html, body { width: 1200px; height: 1000px; overflow: hidden; background: var(--page); }
  .canvas { position: relative; width: 1200px; height: 1000px; }

  .card {
    position: absolute;
    width: 480px; height: 860px;
    background: var(--card);
    box-shadow: 2px 3px 5px rgba(0,0,0,0.35);
    overflow: hidden;
  }
  .card-front { left: 100px; top: 25px; }
  .card-back  { left: 622px; top: 87px; }

  .stripe { position: absolute; top: 0; left: 0; height: 100%; }
  .card-front .stripe { width: 55px; background: var(--stripe-gray); }
  .card-back .stripe  { width: 48px; background: var(--wine); }

  /* front */
  .brand-emblem { position: absolute; left: 198px; top: 262px; }
  .brand-name {
    position: absolute; left: 98px; top: 410px;
    font-family: "Oswald", sans-serif; font-weight: 700;
    color: var(--wine);
    font-size: 52px; line-height: 54px; letter-spacing: 1px;
    text-transform: uppercase;
  }
  .slogan {
    position: absolute; left: 98px; top: 535px;
    font-family: "Pathway Gothic One", sans-serif;
    font-size: 34px; color: var(--ink);
  }
  .website {
    position: absolute; left: 98px; top: 785px;
    font-family: "Oswald", sans-serif; font-weight: 600;
    font-size: 23px; color: var(--wine);
  }

  /* back */
  .brand-small {
    position: absolute; right: 38px; top: 40px;
    text-align: center; width: 140px;
  }
  .brand-small .brand-emblem-small { display: block; margin: 0 auto 6px; }
  .brand-small .brand-name-small {
    font-family: "Oswald", sans-serif; font-weight: 700;
    color: var(--wine); font-size: 18px; line-height: 19px;
    text-transform: uppercase;
  }
  .brand-small .slogan-small {
    font-family: "Pathway Gothic One", sans-serif;
    font-size: 12px; color: var(--ink); margin-top: 2px;
  }

  .contact { position: absolute; right: 47px; text-align: right; color: var(--ink); white-space: nowrap; }
  .person { top: 424px; }
  .person-name {
    font-family: "Oswald", sans-serif; font-weight: 700;
    font-size: 36px; line-height: 46px; color: var(--wine);
  }
  .person-title {
    font-family: "Pathway Gothic One", sans-serif;
    font-size: 27px; line-height: 32px;
  }
  .address, .lines {
    font-family: "Pathway Gothic One", sans-serif;
    font-size: 31px; line-height: 35px;
  }
  .address { top: 595px; }
  .lines { top: 720px; }
</style>
</head>
<body>
<div class="canvas">

  <section class="card card-front">
    <div class="stripe"></div>
    <svg class="brand-emblem" width="84" height="84" viewBox="0 0 84 84" aria-hidden="true">
      <circle cx="42" cy="42" r="40" fill="var(--mark-gray)"/>
    </svg>
    <div class="brand-name">Kranichflug<br>Marketing</div>
    <div class="slogan">Fresh Ground Online Marketing</div>
    <div class="website">www.kranichflug-beispiel.de</div>
  </section>

  <section class="card card-back">
    <div class="stripe"></div>
    <div class="brand-small">
      <svg class="brand-emblem-small" width="34" height="34" viewBox="0 0 34 34" aria-hidden="true">
        <circle cx="17" cy="17" r="16" fill="var(--mark-gray)"/>
      </svg>
      <div class="brand-name-small">Kranichflug<br>Marketing</div>
      <div class="slogan-small">Fresh Ground Online Marketing</div>
    </div>

    <div class="contact person">
      <div class="person-name">Bernhard Olzner</div>
      <div class="person-title">Geschäftsführer | CEO</div>
    </div>

    <div class="contact address">
      Kranichflug Marketing GmbH,<br>
      Lindenweg 23,<br>
      71592 Rebenfeld, Germany
    </div>

    <div class="contact lines">
      Phone: +49 (0) 7421 846 27 05<br>
      Fax: +49 (0) 7421 846 27 88<br>
      e-mail: info@kranichflug-beispiel.de
    </div>
  </section>

</div>
</body>
</html>
```